Digital Transformation Company Trade Show Banners

I am looking for help designing banners for an upcoming trade show. One would be for our company and one would be for our product. I am planning on purchasing retractable banners with a size of 33" x 81". Details are attached.

```html
<!DOCTYPE html>
<html lang="en">
<head>
<meta charset="UTF-8">
<title>Veloraq – Cybersecurity Teams Banner</title>
<link href="https://fonts.googleapis.com/css2?family=Bebas+Neue&family=Poppins:wght@300;600;700;800&display=swap" rel="stylesheet">
<style>
  :root {
    --purple-top: #6a2fb0;
    --purple-mid: #3d2160;
    --ink-dark: #221f2a;
    --ink-deep: #1c1a23;
    --band-purple: #7a22c4;
    --white: #ffffff;
    --rule: rgba(255,255,255,0.45);
    --team-purple: #8e3fd0;
    --team-blue: #2f86e0;
    --team-red: #e0402a;
    --band-ink: #1b1030;
  }
  * { margin: 0; padding: 0; box-sizing: border-box; }
  html, body { width: 1200px; height: 3057px; overflow: hidden; background: #ececec; }
  .banner {
    position: relative;
    width: 1200px;
    height: 3057px;
    overflow: hidden;
    background: linear-gradient(180deg, var(--purple-top) 0%, var(--purple-mid) 22%, var(--ink-dark) 40%, var(--ink-deep) 100%);
    font-family: 'Poppins', sans-serif;
    color: var(--white);
  }
  .brand {
    position: absolute;
    top: 120px;
    left: 360px;
    display: flex;
    align-items: center;
    gap: 28px;
  }
  .brand-dot { width: 84px; height: 84px; border-radius: 50%; background: var(--white); }
  .brand-name { font-weight: 300; font-size: 96px; letter-spacing: 14px; color: var(--white); line-height: 1; }
  .hero-visual {
    position: absolute;
    left: 235px;
    top: 400px;
    width: 720px;
    height: 720px;
    border-radius: 50%;
    background: radial-gradient(circle at 50% 50%, #b676ff 0%, #7a3fe0 40%, #3a1c8a 75%, #241a4a 100%);
  }
  .tagline {
    position: absolute;
    top: 1240px;
    width: 100%;
    text-align: center;
    font-family: 'Bebas Neue', sans-serif;
    font-size: 66px;
    letter-spacing: 0.5px;
    line-height: 1;
  }
  .headline {
    position: absolute;
    top: 1320px;
    width: 100%;
    text-align: center;
    font-family: 'Bebas Neue', sans-serif;
    font-size: 170px;
    line-height: 0.98;
    letter-spacing: 2px;
  }
  .team {
    position: absolute;
    left: 0;
    width: 100%;
    display: flex;
    flex-direction: column;
    align-items: center;
  }
  .team-icon { width: 110px; height: 96px; }
  .team-label { font-weight: 700; font-size: 58px; line-height: 1; margin-top: 18px; letter-spacing: 0.5px; }
  .team-purple { top: 1720px; color: var(--team-purple); }
  .team-blue { top: 1990px; color: var(--team-blue); }
  .team-red { top: 2275px; color: var(--team-red); }
  .team-white { top: 2545px; color: var(--white); }
  .team-label { color: var(--white); }
  .rule { position: absolute; left: 187px; width: 813px; height: 2px; background: var(--rule); }
  .contact-band {
    position: absolute;
    left: 0; bottom: 0;
    width: 100%;
    height: 242px;
    background: var(--band-purple);
  }
  .question {
    position: absolute;
    left: 73px;
    top: 68px;
    font-weight: 800;
    font-size: 54px;
    line-height: 1.1;
    color: var(--band-ink);
  }
  .question-arrow { position: absolute; left: 360px; top: 20px; width: 170px; height: 50px; }
  .contact-icon { position: absolute; width: 52px; height: 52px; }
  .contact-icon.phone { left: 500px; top: 88px; }
  .contact-icon.web { left: 505px; top: 164px; }
  .phone-number { position: absolute; left: 572px; top: 58px; font-weight: 700; font-size: 72px; line-height: 1.1; }
  .web-address { position: absolute; left: 572px; top: 148px; font-weight: 600; font-size: 50px; line-height: 1.1; }
</style>
</head>
<body>
<main class="banner">
  <div class="brand">
    <span class="brand-dot"></span>
    <span class="brand-name">VELORAQ</span>
  </div>

  <div class="hero-visual" role="img" aria-label="Glowing purple digital shield illustration"></div>

  <p class="tagline">INTEGRATED SOLUTIONS DSIGNED FOR ALL</p>
  <h1 class="headline">CYBERSECURITY<br>TEAMS</h1>

  <svg width="0" height="0" style="position:absolute">
    <defs>
      <symbol id="people" viewBox="0 0 110 96">
        <circle cx="55" cy="18" r="16"/>
        <circle cx="22" cy="30" r="13"/>
        <circle cx="88" cy="30" r="13"/>
        <path d="M30 96 V62 a25 25 0 0 1 50 0 V96 Z"/>
        <path d="M2 96 V66 a20 20 0 0 1 30 -17 a32 32 0 0 0 -6 18 V96 Z"/>
        <path d="M108 96 V66 a20 20 0 0 0 -30 -17 a32 32 0 0 1 6 18 V96 Z"/>
      </symbol>
    </defs>
  </svg>

  <div class="team team-purple">
    <svg class="team-icon" fill="var(--team-purple)"><use href="#people"/></svg>
    <span class="team-label">PURPLE TEAMS</span>
  </div>
  <div class="rule" style="top:1930px"></div>

  <div class="team team-blue">
    <svg class="team-icon" fill="var(--team-blue)"><use href="#people"/></svg>
    <span class="team-label">BLUE TEAMS</span>
  </div>
  <div class="rule" style="top:2220px"></div>

  <div class="team team-red">
    <svg class="team-icon" fill="var(--team-red)"><use href="#people"/></svg>
    <span class="team-label">RED TEAMS</span>
  </div>
  <div class="rule" style="top:2505px"></div>

  <div class="team team-white">
    <svg class="team-icon" fill="var(--white)"><use href="#people"/></svg>
    <span class="team-label">WHITE TEAMS</span>
  </div>

  <footer class="contact-band">
    <p class="question">HAVE ANY<br>QUESTIONS?</p>
    <svg class="question-arrow" viewBox="0 0 170 50" fill="none" stroke="#ffffff" stroke-width="3">
      <path d="M5 45 Q80 -5 160 35"/>
      <path d="M148 36 L160 35 L156 24"/>
    </svg>
    <svg class="contact-icon phone" viewBox="0 0 24 24" fill="none" stroke="var(--band-ink)" stroke-width="1.6" stroke-linejoin="round">
      <path d="M5 3h4l2 5-2.5 1.5a11 11 0 0 0 6 6L16 13l5 2v4a2 2 0 0 1-2 2A17 17 0 0 1 3 5a2 2 0 0 1 2-2z"/>
    </svg>
    <svg class="contact-icon web" viewBox="0 0 24 24" fill="none" stroke="var(--band-ink)" stroke-width="1.6">
      <circle cx="12" cy="12" r="9"/>
      <ellipse cx="12" cy="12" rx="4" ry="9"/>
      <path d="M3 12h18M5 7h14M5 17h14"/>
    </svg>
    <p class="phone-number">(555) 210-4837</p>
    <p class="web-address">www.veloraq-demo.io</p>
  </footer>
</main>
</body>
</html>
```